Detail Shop Business card design

i need a business card design for my new detailing company called 'Brisk's Polish Works'. i want an all black and white design . simple, direct and to the point. i want the designer to choose a fitting font to match the logothe front should have logo, address, phone and email and the back side should have a slogan and text indicating that we offer services on anything including cars, trucks, motorcycles and RVs. slogan will read "we take pride in your ride"
maybe also very small on the back side the IG icon with Brisks_Polish_Works

phone 208.417.6352
address 3847 E Larkin Ave
Spokane WA 99214
email: BrisksPolish@mailvexo.com

Target Market(s)

all ages , auto enthusiasts

Industry/Entity Type

Automotive

Contact Information for Business Card

the front should have logo, address, phone and email and the back side should have a slogan and text indicating that we offer services on anything including cars, trucks, motorcycles and RVs. slogan will read "we take pride in your ride"

phone 208.417.6352
address 3847 E Larkin Ave
Spokane WA 99214

Colors
000000
ffffff

Requirements
Must have
• bold font and very simple design with good spacing
Nice to have
• anything creative from the designer indicating we service any types of vehicles
Should not have
• any colors ,

```html
<!DOCTYPE html>
<html lang="en">
<head>
<meta charset="utf-8">
<title>Brisk's Polish Works – Business Card</title>
<link href="https://fonts.googleapis.com/css2?family=Roboto:wght@400;700&family=Squada+One&display=swap" rel="stylesheet">
<style>
  :root {
    --ink: #000000;
    --paper: #ffffff;
    --card-tint: #f4f4f4;
    --muted: #555555;
    --rule: #c8c8c8;
    --backdrop: #e6e6e6;
    --art-light: #d9d9d9;
    --art-mid: #8c8c8c;
    --art-dark: #3c3c3c;
  }
  * { margin: 0; padding: 0; box-sizing: border-box; }
  html, body { width: 1200px; height: 960px; overflow: hidden; }
  body {
    background: var(--backdrop);
    font-family: "Roboto", Arial, sans-serif;
    color: var(--ink);
    position: relative;
  }
  .card {
    position: absolute;
    width: 600px;
    height: 342px;
    background: var(--card-tint);
    box-shadow: 0 3px 8px rgba(0,0,0,0.25);
    overflow: hidden;
  }
  .card--front { left: 314px; top: 113px; }
  .card--back  { left: 311px; top: 472px; }

  /* Front */
  .brand-mark {
    position: absolute;
    left: 78px; top: 88px;
    width: 200px; height: 174px;
    display: flex; flex-direction: column;
    align-items: center; justify-content: center; gap: 12px;
  }
  .brand-mark__dot {
    width: 26px; height: 26px;
    border-radius: 50%;
    background: var(--ink);
  }
  .brand-mark__name {
    font-weight: 700;
    font-size: 30px;
    line-height: 1.05;
    text-align: center;
    text-transform: uppercase;
    color: var(--ink);
  }
  .divider {
    position: absolute;
    left: 306px; top: 85px;
    width: 1px; height: 178px;
    background: var(--rule);
  }
  .contact {
    position: absolute;
    left: 334px; top: 84px;
  }
  .contact__name {
    font-weight: 700;
    font-size: 21px;
    letter-spacing: 0.3px;
    line-height: 1.1;
  }
  .contact__title {
    font-size: 15px;
    color: var(--muted);
    margin-top: 1px;
  }
  .contact__address {
    font-size: 14px;
    color: var(--muted);
    line-height: 19px;
    margin-top: 12px;
  }
  .contact__list {
    list-style: none;
    margin-top: 12px;
    font-size: 14px;
    color: var(--muted);
  }
  .contact__list li {
    display: flex; align-items: center;
    height: 19px;
  }
  .contact__list svg {
    width: 12px; height: 12px;
    margin-right: 10px;
    fill: var(--ink);
    flex: none;
  }
  .edge-line {
    position: absolute;
    left: 0; width: 100%;
    top: 320px; height: 2px;
    background: var(--ink);
  }
  .edge-band {
    position: absolute;
    left: 0; width: 100%;
    top: 328px; height: 14px;
    background: var(--ink);
  }

  /* Back */
  .services {
    position: absolute;
    left: 0; width: 100%;
    top: 50px;
    text-align: center;
    font-family: "Squada One", "Arial Narrow", sans-serif;
    font-size: 17px;
    letter-spacing: 0;
  }
  .vehicle-art {
    position: absolute;
    left: 20px; top: 112px;
    width: 552px; height: 190px;
    background: radial-gradient(ellipse at 50% 45%, var(--art-mid) 0%, var(--art-dark) 55%, var(--art-light) 100%);
    border-radius: 50% 50% 30% 30% / 40% 40% 30% 30%;
    opacity: 0.55;
  }
  .ground {
    position: absolute;
    left: 0; bottom: 0;
    width: 600px; height: 50px;
  }
  .slogan {
    position: absolute;
    left: 0; width: 100%;
    top: 306px;
    text-align: center;
    color: var(--paper);
    font-weight: 700;
    font-size: 17px;
    letter-spacing: 0.6px;
  }
</style>
</head>
<body>

  <section class="card card--front" aria-label="Business card front">
    <div class="brand-mark">
      <span class="brand-mark__dot"></span>
      <span class="brand-mark__name">Brisk's<br>Polish Works</span>
    </div>

    <div class="divider"></div>

    <div class="contact">
      <p class="contact__name">DALE MERROW</p>
      <p class="contact__title">CEO/FOUNDER</p>
      <p class="contact__address">3847 E Larkin Ave<br>Spokane WA 99214</p>
      <ul class="contact__list">
        <li>
          <svg viewBox="0 0 24 24" aria-hidden="true"><path d="M6.6 10.8a15.1 15.1 0 0 0 6.6 6.6l2.2-2.2a1 1 0 0 1 1-.25 11.4 11.4 0 0 0 3.6.57 1 1 0 0 1 1 1V20a1 1 0 0 1-1 1A17 17 0 0 1 3 4a1 1 0 0 1 1-1h3.5a1 1 0 0 1 1 1c0 1.25.2 2.45.57 3.57a1 1 0 0 1-.25 1z"/></svg>
          208.417.6352
        </li>
        <li>
          <svg viewBox="0 0 24 24" aria-hidden="true"><path d="M7 1h10a2 2 0 0 1 2 2v18a2 2 0 0 1-2 2H7a2 2 0 0 1-2-2V3a2 2 0 0 1 2-2zm0 3v14h10V4zm5 15.5a1.2 1.2 0 1 0 0 2.4 1.2 1.2 0 0 0 0-2.4z"/></svg>
          208 552 7180
        </li>
        <li>
          <svg viewBox="0 0 24 24" aria-hidden="true"><path d="M2 5h20v14H2zm2 2v.5l8 5 8-5V7l-8 5z"/></svg>
          BrisksPolish@mailvexo.com
        </li>
        <li>
          <svg viewBox="0 0 24 24" aria-hidden="true"><circle cx="12" cy="12" r="10"/></svg>
          www.briskspolishworks.com
        </li>
      </ul>
    </div>

    <div class="edge-line"></div>
    <div class="edge-band"></div>
  </section>

  <section class="card card--back" aria-label="Business card back">
    <p class="services">we offer services on anything including cars, trucks, motorcycles &amp; RVs</p>

    <div class="vehicle-art" role="img" aria-label="Black and white illustration of a hot rod car in side view"></div>

    <svg class="ground" viewBox="0 0 600 50" preserveAspectRatio="none" aria-hidden="true">
      <path d="M0 50 L0 34 Q90 6 300 4 Q510 6 600 30 L600 50 Z" fill="#000000"/>
    </svg>

    <p class="slogan">WE TAKE PRIDE IN YOUR RIDE</p>
  </section>

</body>
</html>
```